Dental Practice Billboard Design

We are a newer dental practice in need of a simple but appealing billboard for our growing dental practice to attract new patients. The practice is owned by husband and wife dentists and is family friendly in a small town in Kentucky. We try to be very friendly and caring to our patients. Would prefer a blue background for the billboard and our tooth logo to be prominent. We are partial to the Patua One font used in the image below but please feel free to tweak it as you deem necessary. The shape of the uppercase D and lowercase g are why we like that font, so fonts with a similarly shaped “D” and “g” would work as well. Please include our phone number (555) 847-1390. Please see our website Harlowbrookdentistry.example for more info on the practice if needed. Thank you! Looking forward to seeing your creation.
Updates

The dimensions will be 12ft x 24ft (3.6576m x 7.3152m). Apologies for not including this in the original prompt. Thank you all for your submissions.

Industry/Entity Type

Dental

Font styles to use
Other font styles liked:
• Patua One

Colors
0054AA
0677BA
7BADD7
CADEEF
E8F1F8
0094D4
00A9DD
6FCCEA
C7EBF8
E9F6FB
00AB8E
00BBA5
67D7C9
C6EFE9
E9F9F6
59FF00
82FF00
B8FF75
E3FFCB
F4FFEA

Requirements
Must have
• Phone number, website, Logo, Practice name “Harlow Brook Dentistry”
Should not have
• A tagline or slogan

```html
<!DOCTYPE html>
<html lang="en">
<head>
<meta charset="utf-8">
<title>Harlow Brook Dentistry – Billboard</title>
<link href="https://fonts.googleapis.com/css2?family=Patua+One&display=swap" rel="stylesheet">
<style>
  :root {
    --brand-blue: #0054aa;
    --brand-blue-dark: #0a4aa0;
    --brand-green: #17b21a;
    --text-white: #ffffff;
    --page-bg: #ffffff;
  }
  * { margin: 0; padding: 0; box-sizing: border-box; }
  html, body {
    width: 1071px;
    height: 1200px;
    overflow: hidden;
    background: var(--page-bg);
  }
  body {
    position: relative;
    font-family: "Patua One", Georgia, serif;
    color: var(--text-white);
  }
  .billboard {
    position: absolute;
    left: 36px;
    top: 362px;
    width: 1000px;
    height: 476px;
    background: var(--brand-blue);
    overflow: hidden;
    box-shadow: 0 4px 14px rgba(0, 0, 0, 0.18);
  }
  .billboard__waves {
    position: absolute;
    inset: 0;
    width: 100%;
    height: 100%;
  }
  .brand-lockup {
    position: absolute;
    top: 62px;
    left: 0;
    width: 100%;
    display: flex;
    justify-content: center;
    align-items: center;
    gap: 30px;
  }
  .brand-lockup__mark {
    width: 190px;
    height: 190px;
    border-radius: 50%;
    background: var(--brand-green);
    flex: none;
  }
  .brand-lockup__name {
    font-size: 84px;
    line-height: 92px;
    color: var(--text-white);
    white-space: nowrap;
  }
  .contact {
    position: absolute;
    right: 32px;
    color: var(--text-white);
    display: flex;
    align-items: center;
    gap: 12px;
    white-space: nowrap;
  }
  .contact--phone { top: 374px; font-size: 38px; }
  .contact--web { top: 428px; font-size: 29px; }
  .contact__icon { flex: none; }
</style>
</head>
<body>
  <section class="billboard" aria-label="Harlow Brook Dentistry billboard">
    <svg class="billboard__waves" viewBox="0 0 1000 476" preserveAspectRatio="none" aria-hidden="true">
      <path d="M0,398 C260,410 420,372 470,362 C340,400 180,412 0,404 Z" fill="var(--brand-green)"/>
      <path d="M0,428 C300,436 620,360 1000,356 L1000,476 L0,476 Z" fill="var(--brand-green)"/>
      <path d="M0,418 C260,428 520,372 880,340 C560,378 300,426 0,424 Z" fill="var(--brand-blue)"/>
      <path d="M110,446 C400,440 650,380 880,342 C650,388 400,446 110,452 Z" fill="var(--brand-blue-dark)"/>
    </svg>

    <div class="brand-lockup">
      <span class="brand-lockup__mark" aria-hidden="true"></span>
      <h1 class="brand-lockup__name" style="font-weight:400">Harlow Brook<br>Dentistry</h1>
    </div>

    <div class="contact contact--phone">
      <svg class="contact__icon" width="40" height="40" viewBox="0 0 40 40" aria-hidden="true">
        <circle cx="20" cy="20" r="17.5" fill="none" stroke="#fff" stroke-width="3"/>
        <path d="M14 11 l4 0 l1.5 5 l-2.5 2 c1.2 2.6 3 4.4 5.5 5.5 l2-2.5 l5 1.5 l0 4 c-9 1-17-7-15.5-15.5 z" fill="#fff"/>
      </svg>
      <span>(555) 847-1390</span>
    </div>

    <div class="contact contact--web">
      <svg class="contact__icon" width="36" height="36" viewBox="0 0 36 36" aria-hidden="true">
        <circle cx="18" cy="18" r="15.5" fill="none" stroke="#fff" stroke-width="3"/>
        <circle cx="18" cy="18" r="9.5" fill="none" stroke="#fff" stroke-width="2"/>
        <path d="M8.5 18 h19 M18 8.5 c-4 5-4 14 0 19 M18 8.5 c4 5 4 14 0 19" fill="none" stroke="#fff" stroke-width="1.6"/>
      </svg>
      <span>Harlowbrookdentistry.example</span>
    </div>
  </section>
</body>
</html>
```